Business Card for Polygraph business in Africa

Business Card . Polygraph Examiner based in Tanzania, East Africa.
Business Card will be used to disseminate contact information to potential clients.
It should convey that I am a professional specifically in the polygraph field and perform my work with integrity.

I have attached the business card that I'm currently using, which I threw together myself initially. It's not professional enough.

Target Market(s)

Banks, Accounting Firms, Government Ministries, Gas, Oil, & Gemstone Mining Concerns, Wildlife Conservation NGOs, International companies located in East Africa.

Industry/Entity Type

Business

Contact Information for Business Card

Veritrace Kilonga
Miriam Holloway
PO Box 48317
Arusha, Tanzania
+255 612 839 274
miriamholloway@postvale.example

Colors
00a990
f37122
faa54b

Requirements
Must have
• - Veritrace Kilonga (with the word "Polygraph" being more prominent than the word "Tanzania")
• - Forensic Examinations
• - Employment Screening
• - Should contain a logo of the Continental Truthline Society (of which I'm a member)
• - I would like an accent design (such as the polygraph "squiggles" of a cardio tracing or such as that)
• - My contact information (less prominent, but large enough to read legibly). I would also consider putting the contact information on the second side of the card.
Nice to have
• My color suggestions are changeable.
Should not have
• Anything "cutesy" or "cartoonish"

```html
<!DOCTYPE html>
<html lang="en">
<head>
<meta charset="utf-8">
<title>Veritrace Kilonga – Business Card</title>
<link rel="stylesheet" href="https://fonts.googleapis.com/css2?family=Roboto:wght@400;500&family=Roboto+Condensed:wght@400;700&display=swap">
<style>
  :root {
    --brand-blue: #0b4ea6;
    --brand-blue-deep: #083f8c;
    --card-white: #fbfbfb;
    --ink-grey: #4a4f57;
    --badge-tint: #eef1fa;
    --backdrop: #e9e6e1;
  }
  * { box-sizing: border-box; margin: 0; padding: 0; }
  html, body { width: 1200px; height: 886px; overflow: hidden; }
  body {
    background: var(--backdrop);
    font-family: "Roboto", sans-serif;
    position: relative;
  }
  .card {
    position: absolute;
    top: 288px;
    width: 540px;
    height: 310px;
    border-radius: 22px;
    overflow: hidden;
    box-shadow: 0 10px 28px rgba(0,0,0,0.18);
  }
  /* Front */
  .card-front { left: 40px; background: var(--card-white); }
  .name-band {
    position: absolute;
    left: 0; top: 96px;
    width: 236px; height: 62px;
    background: var(--brand-blue);
    padding: 9px 0 0 32px;
    color: #fff;
  }
  .holder-name {
    font-family: "Roboto Condensed", sans-serif;
    font-weight: 700;
    font-size: 21px;
    letter-spacing: 0.2px;
    line-height: 1.05;
  }
  .holder-company {
    font-family: "Roboto Condensed", sans-serif;
    font-size: 14px;
    line-height: 1.3;
  }
  .brand-mark {
    position: absolute;
    display: flex;
    align-items: center;
    gap: 10px;
  }
  .brand-mark .brand-dot {
    width: 30px; height: 30px;
    border-radius: 50%;
    border: 3px solid currentColor;
  }
  .brand-mark .brand-name {
    font-family: "Roboto", sans-serif;
    font-weight: 500;
    font-size: 26px;
    white-space: nowrap;
  }
  .card-front .brand-mark { left: 246px; top: 110px; color: var(--brand-blue); }
  .member-badge {
    position: absolute;
    right: 38px; top: 38px;
    width: 58px; height: 58px;
    border-radius: 50%;
    background: var(--badge-tint);
    border: 3px solid var(--brand-blue);
  }
  .postal-address {
    position: absolute;
    right: 30px; top: 176px;
    font-size: 14px;
    color: var(--ink-grey);
  }
  .contact-list {
    position: absolute;
    left: 34px; bottom: 28px;
    list-style: none;
    font-size: 13.5px;
    color: var(--ink-grey);
  }
  .contact-list li { display: flex; align-items: center; gap: 9px; line-height: 1.5; }
  .contact-list svg { width: 11px; height: 11px; fill: var(--brand-blue); flex: none; }

  /* Back */
  .card-back {
    left: 620px;
    background: linear-gradient(135deg, var(--brand-blue) 0%, var(--brand-blue-deep) 100%);
    color: #fff;
  }
  .card-back .brand-mark { left: 50%; top: 118px; transform: translateX(-50%); color: #fff; }
  .card-back .brand-mark .brand-name { font-size: 34px; }
  .card-back .brand-mark .brand-dot { width: 38px; height: 38px; }
  .services {
    position: absolute;
    left: 0; right: 0; bottom: 44px;
    text-align: center;
    font-size: 14px;
    letter-spacing: 0.3px;
  }
  .services .divider { margin: 0 10px; opacity: 0.7; }
</style>
</head>
<body>
  <section class="card card-front" aria-label="Card front">
    <div class="name-band">
      <p class="holder-name">MIRIAM HOLLOWAY</p>
      <p class="holder-company">VERITRACE KILONGA</p>
    </div>
    <div class="brand-mark">
      <span class="brand-dot"></span>
      <span class="brand-name">Veritrace Kilonga</span>
    </div>
    <div class="member-badge" role="img" aria-label="Continental Truthline Society membership badge"></div>
    <p class="postal-address">PO Box 48317, Arusha, Tanzania</p>
    <ul class="contact-list">
      <li>
        <svg viewBox="0 0 24 24" aria-hidden="true"><path d="M6.6 10.8a15 15 0 0 0 6.6 6.6l2.2-2.2a1 1 0 0 1 1-.25 11.4 11.4 0 0 0 3.6.57 1 1 0 0 1 1 1V20a1 1 0 0 1-1 1A17 17 0 0 1 3 4a1 1 0 0 1 1-1h3.5a1 1 0 0 1 1 1c0 1.25.2 2.45.57 3.57a1 1 0 0 1-.25 1z"/></svg>
        +255 612 839 274
      </li>
      <li>
        <svg viewBox="0 0 24 24" aria-hidden="true"><path d="M2 5h20v14H2z M2 5l10 8 10-8" /></svg>
        miriamholloway@postvale.example
      </li>
      <li>
        <svg viewBox="0 0 24 24" aria-hidden="true"><circle cx="12" cy="12" r="10"/></svg>
        www.miriamholloway.example
      </li>
    </ul>
  </section>

  <section class="card card-back" aria-label="Card back">
    <div class="brand-mark">
      <span class="brand-dot"></span>
      <span class="brand-name">Veritrace Kilonga</span>
    </div>
    <p class="services">Forensic Examinations<span class="divider">|</span>Employment Screening</p>
  </section>
</body>
</html>
```